Vorn upkeep KT Solar Venture

Solar power system install
Services and maintenance
wiring, Rewinding and Renovation
Switch Board Upgrade
Power and lighting point
t doesn’t matter how much you spend on quality parts, your solar system will let you down if your design and installation are sub-par. Have your solar system tailored and installed by our Master Electrician and Bright Grid Guild Accredited team.

Target Market(s)

sales and installed

Industry/Entity Type

Solar install and retailer

Contact Information for Business Card

Name , Email, Phone Number ,Business address,

Font styles to use
Serif

Colors
0054AA
0677BA
7BADD7
CADEEF
E8F1F8

Requirements
Must have
• clear and bright
Nice to have
• new design
Should not have
• unclear pictures

```html
<!DOCTYPE html>
<html lang="en">
<head>
<meta charset="utf-8">
<title>Vorn upkeep – KT Solar Venture business card</title>
<link href="https://fonts.googleapis.com/css2?family=Roboto:wght@400;700&display=swap" rel="stylesheet">
<style>
  :root{
    --bg:#2e2e2e;
    --card:#f1f2f3;
    --blue-deep:#0054AA;
    --blue:#0677BA;
    --blue-soft:#7BADD7;
    --green:#1f8a3a;
    --green-light:#6fb33a;
    --ink:#1d1d1f;
    --band-text:#f2f7fb;
  }
  *{margin:0;padding:0;box-sizing:border-box}
  html,body{width:1200px;height:1138px;overflow:hidden;background:var(--bg);font-family:"Roboto",Arial,sans-serif;color:var(--ink)}
  .card{position:absolute;width:622px;height:375px;border-radius:14px;background:linear-gradient(135deg,#f6f7f8,#e9ebed);overflow:hidden}
  .card--front{left:274px;top:186px}
  .card--back{left:276px;top:608px}

  .brand{position:absolute;display:flex;align-items:center;gap:18px}
  .brand__dot{border-radius:50%;background:var(--blue);flex:none}
  .brand__name{font-family:"Roboto",Arial,sans-serif;font-weight:700;color:var(--blue-deep);text-transform:uppercase;line-height:1.05}
  .card--front .brand{left:104px;top:78px}
  .card--front .brand__dot{width:92px;height:92px}
  .card--front .brand__name{font-size:34px}
  .card--back .brand{left:22px;top:38px}
  .card--back .brand__dot{width:104px;height:104px}
  .card--back .brand__name{font-size:44px}

  .services{position:absolute;left:0;top:239px;width:100%;height:74px;background:linear-gradient(90deg,var(--green-light) 0%,#3d9a5a 35%,var(--blue) 70%,var(--blue-deep) 100%);color:var(--band-text);font-size:16.5px;text-align:center;display:flex;flex-direction:column;justify-content:center;gap:5px}
  .website{position:absolute;left:0;top:332px;width:100%;display:flex;justify-content:center;align-items:center;gap:28px;font-size:16px}
  .website__rule{width:80px;height:2px}
  .website__rule--blue{background:linear-gradient(90deg,transparent,var(--blue))}
  .website__rule--green{background:linear-gradient(90deg,var(--green-light),transparent)}

  .person{position:absolute;left:35px;top:210px}
  .person__name{font-size:26px;font-weight:700;color:var(--blue-deep)}
  .person__role{font-size:16px;margin-top:4px}
  .address{position:absolute;left:35px;top:292px;font-size:16px;line-height:24px}
  .contacts{position:absolute;left:338px;top:230px;list-style:none;font-size:16.5px;line-height:24px}
  .contacts li{display:flex;align-items:center;gap:14px}
  .contacts svg{width:16px;height:16px;flex:none}
  .footer-bands{position:absolute;left:0;top:0;width:622px;height:375px}
  .footer-tag{position:absolute;left:339px;top:339px;font-size:16.5px;color:var(--band-text)}
</style>
</head>
<body>

<section class="card card--front" aria-label="Business card front">
  <div class="brand">
    <span class="brand__dot"></span>
    <span class="brand__name">Vorn upkeep<br>KT Solar Venture</span>
  </div>
  <div class="services">
    <p>Solar Power System Install &nbsp;|&nbsp; Wiring, Rewinding &amp; Renovation</p>
    <p>Services &amp; Maintenance &nbsp;|&nbsp; Switch Board Upgrade &nbsp;|&nbsp; Power &amp; Lighting Point</p>
  </div>
  <div class="website">
    <span class="website__rule website__rule--blue"></span>
    <span>www.ktsolarventure.com</span>
    <span class="website__rule website__rule--green"></span>
  </div>
</section>

<section class="card card--back" aria-label="Business card back">
  <div class="brand">
    <span class="brand__dot"></span>
    <span class="brand__name">Vorn upkeep<br>KT Solar Venture</span>
  </div>

  <div class="person">
    <p class="person__name">Mara Lind Ostby</p>
    <p class="person__role">Managing Director</p>
  </div>
  <p class="address">88 Ridgeway Rd., Fernvale,<br>Lakeport, US 204518</p>

  <ul class="contacts">
    <li><svg viewBox="0 0 16 16"><path fill="#1f8a3a" d="M2 5c0-2 2-3 6-3s6 1 6 3v1h-3V4.5H5V6H2zM4 7h8l2 6H2z"/></svg>555-014-2290</li>
    <li><svg viewBox="0 0 16 16"><rect x="1" y="3" width="14" height="10" fill="#1f8a3a"/><path d="M1 3l7 6 7-6" stroke="#fff" stroke-width="1.4" fill="none"/></svg>mara@ktsolarventure.com</li>
    <li><svg viewBox="0 0 16 16"><circle cx="8" cy="8" r="7" fill="#1f8a3a"/><path d="M1 8h14M8 1c-3 3-3 11 0 14M8 1c3 3 3 11 0 14" stroke="#fff" stroke-width="1" fill="none"/></svg>www.ktsolarventure.com</li>
  </ul>

  <svg class="footer-bands" viewBox="0 0 622 375" aria-hidden="true">
    <defs>
      <linearGradient id="greenBand" x1="0" x2="1">
        <stop offset="0" stop-color="#6fb33a"/><stop offset="1" stop-color="#1f8a3a"/>
      </linearGradient>
      <linearGradient id="blueBand" x1="0" x2="1">
        <stop offset="0" stop-color="#0677BA"/><stop offset="1" stop-color="#0054AA"/>
      </linearGradient>
    </defs>
    <rect x="0" y="360" width="300" height="15" fill="url(#greenBand)"/>
    <path d="M296 328H622V375H276L288 336Q291 328 296 328Z" fill="url(#blueBand)"/>
  </svg>
  <p class="footer-tag">Solar power system install</p>
</section>

</body>
</html>
```